Beer Label Design for Quillfern Beer Company

Hello, we are looking for a beer label design for our first bottle release, Zorbitude Barleywine. We have attached a label my illustrator friend did which was rejected by the FRL because it says "Harbor Dawnglow" which could be confused with tequila apparently. Anyway due to a computer crash we lost the original vector file so cannot edit. Since we have a do over we are looking for new ideas. We are pretty much open to anything as long as it contains:
-Original label information
-'Coastal Starfall' 'Ale Aged in Tequila Barrels' underneath replacing 'Harbor Dawnglow"
-Quillfern Beer Company somewhere on label
-can't be obscene or it will not get approved by FRL
Attached is the original label as well as our logo and other graphics for inspiration.

Get creative and look forward to working with you.

Cheers!

Industry/Entity Type

Brewery

Requirements
Must have
• -Fit to attached template for printing (sorry forgot to attach this last night!) Necker can be used for Quillfern Beer Company but not a must have for design if it fits on square label.
• -Stand out in a row of bottles
• -Original label information
• -'Coastal Starfall' 'Ale Aged in Tequila Barrels' underneath replacing 'Harbor Dawnglow"
• -Quillfern Beer Company somewhere on label
• -can't be obscene or it will not get approved by FRL
Nice to have
• What is a zorbitude? We have no idea either but it won the contest we held to name our anniversary beer. We like rockets, ufo's, old school planets. Our preference is vintage but are open minded.

```html
<!DOCTYPE html>
<html lang="en">
<head>
<meta charset="utf-8">
<title>Zorbitude Barleywine Label</title>
<link href="https://fonts.googleapis.com/css2?family=Bebas+Neue&family=Oswald:wght@500&display=swap" rel="stylesheet">
<style>
  :root {
    --canvas-bg: #e9e6e2;
    --label-black: #141213;
    --badge-red: #d8251f;
    --ink-white: #f4f1ec;
  }
  html, body {
    margin: 0;
    padding: 0;
    width: 1200px;
    height: 900px;
    overflow: hidden;
    background: var(--canvas-bg);
  }
  .canvas {
    width: 1200px;
    height: 900px;
    display: flex;
    align-items: center;
    justify-content: center;
  }
  .beer-label {
    width: 720px;
    height: 690px;
    display: block;
  }
  .label-field { fill: var(--label-black); }
  .burst-teeth { fill: var(--badge-red); }
  .burst-core { fill: var(--label-black); }
  .badge-disk { fill: var(--badge-red); }
  .badge-dash {
    fill: none;
    stroke: var(--ink-white);
    stroke-width: 3;
    stroke-dasharray: 9 7;
  }
  .brand-arc {
    font-family: "Oswald", sans-serif;
    font-weight: 500;
    font-size: 22px;
    letter-spacing: 2px;
    fill: var(--ink-white);
  }
  .banner-band { fill: var(--label-black); }
  .banner-rule {
    stroke: var(--badge-red);
    stroke-width: 3;
    stroke-dasharray: 12 6;
  }
  .product-name {
    font-family: "Bebas Neue", sans-serif;
    font-size: 96px;
    letter-spacing: 1px;
    fill: var(--ink-white);
  }
  .spec-text {
    font-family: "Bebas Neue", sans-serif;
    font-size: 30px;
    fill: var(--ink-white);
  }
  .sub-name {
    font-family: "Bebas Neue", sans-serif;
    font-size: 44px;
    letter-spacing: 2px;
    fill: var(--badge-red);
  }
  .sub-style {
    font-family: "Oswald", sans-serif;
    font-weight: 500;
    font-size: 20px;
    letter-spacing: 3px;
    fill: var(--ink-white);
  }
</style>
</head>
<body>
<main class="canvas">
  <svg class="beer-label" viewBox="0 0 720 690" xmlns="http://www.w3.org/2000/svg">
    <defs>
      <polygon id="tooth" points="-16,-236 0,-264 16,-236"/>
      <radialGradient id="artTone" cx="50%" cy="45%" r="60%">
        <stop offset="0%" stop-color="#e8443c"/>
        <stop offset="100%" stop-color="#8e100c"/>
      </radialGradient>
      <path id="brandPath" d="M 210 290 A 150 150 0 0 1 510 290"/>
    </defs>

    <rect class="label-field" x="0" y="0" width="720" height="690"/>

    <g class="starburst" transform="translate(360 290)">
      <circle class="burst-teeth" r="240"/>
      <g class="burst-teeth">
        <use href="#tooth" transform="rotate(0)"/><use href="#tooth" transform="rotate(10)"/>
        <use href="#tooth" transform="rotate(20)"/><use href="#tooth" transform="rotate(30)"/>
        <use href="#tooth" transform="rotate(40)"/><use href="#tooth" transform="rotate(50)"/>
        <use href="#tooth" transform="rotate(60)"/><use href="#tooth" transform="rotate(70)"/>
        <use href="#tooth" transform="rotate(80)"/><use href="#tooth" transform="rotate(90)"/>
        <use href="#tooth" transform="rotate(100)"/><use href="#tooth" transform="rotate(110)"/>
        <use href="#tooth" transform="rotate(120)"/><use href="#tooth" transform="rotate(130)"/>
        <use href="#tooth" transform="rotate(140)"/><use href="#tooth" transform="rotate(150)"/>
        <use href="#tooth" transform="rotate(160)"/><use href="#tooth" transform="rotate(170)"/>
        <use href="#tooth" transform="rotate(180)"/><use href="#tooth" transform="rotate(190)"/>
        <use href="#tooth" transform="rotate(200)"/><use href="#tooth" transform="rotate(210)"/>
        <use href="#tooth" transform="rotate(220)"/><use href="#tooth" transform="rotate(230)"/>
        <use href="#tooth" transform="rotate(240)"/><use href="#tooth" transform="rotate(250)"/>
        <use href="#tooth" transform="rotate(260)"/><use href="#tooth" transform="rotate(270)"/>
        <use href="#tooth" transform="rotate(280)"/><use href="#tooth" transform="rotate(290)"/>
        <use href="#tooth" transform="rotate(300)"/><use href="#tooth" transform="rotate(310)"/>
        <use href="#tooth" transform="rotate(320)"/><use href="#tooth" transform="rotate(330)"/>
        <use href="#tooth" transform="rotate(340)"/><use href="#tooth" transform="rotate(350)"/>
      </g>
      <circle class="burst-core" r="232"/>
      <circle class="badge-disk" r="205"/>
      <circle class="badge-dash" r="190"/>
    </g>

    <circle cx="360" cy="312" r="130" fill="url(#artTone)" role="img"
            aria-label="Illustration of a helmeted space traveller with a rocket visor"/>

    <text class="brand-arc" text-anchor="middle">
      <textPath href="#brandPath" startOffset="50%">QUILLFERN BEER COMPANY</textPath>
    </text>

    <g class="name-banner">
      <rect class="banner-band" x="0" y="400" width="720" height="92"/>
      <line class="banner-rule" x1="0" y1="404" x2="720" y2="404"/>
      <line class="banner-rule" x1="0" y1="488" x2="720" y2="488"/>
      <text class="spec-text" x="42" y="442">22</text>
      <text class="spec-text" x="42" y="472">OZ</text>
      <text class="product-name" x="360" y="482" text-anchor="middle">ZORBITUDE</text>
      <text class="spec-text" x="620" y="442">ALC</text>
      <text class="spec-text" x="620" y="472">12.8%</text>
    </g>

    <g class="style-lines">
      <text class="sub-name" x="360" y="614" text-anchor="middle">COASTAL STARFALL</text>
      <text class="sub-style" x="360" y="652" text-anchor="middle">ALE AGED IN TEQUILA BARRELS</text>
    </g>
  </svg>
</main>
</body>
</html>
```